FinTech company looking to revamp and expand client-facing interface for our financial models

Pellworth Engines currently has a very simple website that allows clients to interact with our financial models. We are looking to completely redesign the current site and add several extra pages to provide extra functionality. We want the design to have a modern, slick feel, that will work on both a desktop or a tablet. It should be straightforward for clients to move between different pages at any time, and clear from the layout how to interact with the more advanced features. We have included screenshots of existing pages in the attached design brief, as well as sketches of the functionality required by the new pages, but can't provide a direct link to the current site.
Target Market(s)
Professional investors that will be paying to access the interface
Industry/Entity Type
Finance
Number of Pages Required
4 page
Colors
Designer to choose colors to be used in the design.
Look and feel
Each slider illustrates characteristics of the customer's brand and the style your logo design should communicate.

```html
<!DOCTYPE html>
<html lang="en">
<head>
<meta charset="utf-8">
<title>Pellworth Engines – Factors</title>
<link href="https://fonts.googleapis.com/css2?family=Montserrat:wght@600;700;800&family=Open+Sans:wght@400;600;700&display=swap" rel="stylesheet">
<style>
:root{
  --page:#e4e4e4;
  --navy:#1c3f5d;
  --ink:#2b4a66;
  --orange:#f5b03b;
  --black:#000;
  --white:#fff;
  --dark:#222;
}
*{box-sizing:border-box;margin:0;padding:0}
html,body{width:1200px;height:1136px;overflow:hidden;background:var(--page)}
body{position:relative;font-family:"Open Sans",sans-serif}
.screen{position:absolute;left:63px;width:1074px;background:var(--white)}
.screen--factors{top:81px;height:501px}
.screen--selection{top:642px;height:407px}
.topbar{position:absolute;left:0;top:0;width:100%;background:var(--navy)}
.screen--factors .topbar{height:84px}
.screen--selection .topbar{height:87px}
.brand{position:absolute;left:99px;top:50%;transform:translateY(-50%);font-family:"Montserrat",sans-serif;font-weight:800;font-size:24px;color:var(--white);letter-spacing:.3px}
.pill{position:absolute;height:28px;border-radius:14px;background:var(--white);color:var(--navy);font-family:"Open Sans",sans-serif;font-weight:700;font-size:11.5px;display:flex;align-items:center;justify-content:center}
.views{position:absolute;top:0;height:100%;display:flex;align-items:center;font-family:"Open Sans",sans-serif;font-weight:700;font-size:12.5px;color:var(--white)}
.views .active{background:var(--black);color:var(--orange);height:100%;width:84px;display:flex;align-items:center;justify-content:center;margin-right:11px}
.views span{margin-right:14px}
.tabs{position:absolute;left:0;width:100%;height:60px;display:flex;justify-content:space-between}
.tab{width:354px;height:100%;background:var(--orange);box-shadow:0 3px 4px rgba(0,0,0,.18);display:flex;align-items:center;justify-content:center;gap:9px;font-family:"Montserrat",sans-serif;font-weight:700;font-size:17.5px;color:var(--white)}
.tab svg{width:20px;height:20px;fill:var(--white)}
.grid{position:absolute;left:100px;border-collapse:collapse;table-layout:fixed;color:var(--ink);font-size:14px;text-align:center}
.grid th{background:var(--navy);color:var(--white);font-weight:400;border-left:1px solid var(--white)}
.grid th:first-child{border-left:none}
.grid td{border:1px solid var(--navy)}
.grid--factors{top:144px;width:870px}
.grid--factors th{height:60px}
.grid--factors td{height:45.4px}
.grid--selection{top:178px;width:880px;color:var(--dark)}
.grid--selection th{height:64px}
.grid--selection td{height:37.4px}
.footnote{position:absolute;left:0;width:100%;text-align:center;font-size:14px;color:var(--dark)}
.code{position:absolute;font-size:13px;color:var(--dark)}
</style>
</head>
<body>

<section class="screen screen--factors">
  <header class="topbar">
    <div class="brand">PELLWORTH ENGINES</div>
    <div class="pill" style="left:422px;top:27px;width:165px">STAR 1 THRESHOLD : 10</div>
    <div class="pill" style="left:594px;top:27px;width:165px">STAR 2 THRESHOLD : 10</div>
    <nav class="views" style="left:779px"><span class="active">FACTORS</span><span>250D</span><span>83D</span><span>42D</span></nav>
  </header>
  <nav class="tabs" style="top:84px">
    <div class="tab"><svg viewBox="0 0 20 20"><path d="M10 2 1 10h3v8h4.5v-5h3v5H16v-8h3z"/></svg>MODELS</div>
    <div class="tab"><svg viewBox="0 0 20 20"><circle cx="10" cy="10" r="7.5" fill="none" stroke="#fff" stroke-width="4" stroke-dasharray="3 2.9"/><circle cx="10" cy="10" r="6"/><circle cx="10" cy="10" r="2.3" fill="#f5b03b"/></svg>SENSITIVITIES</div>
    <div class="tab"><svg viewBox="0 0 20 20"><path d="M10 18 2.3 10.3A4.6 4.6 0 0 1 10 4a4.6 4.6 0 0 1 7.7 6.3z"/></svg>FAVORITES</div>
  </nav>
  <table class="grid grid--factors">
    <thead><tr><th>FACTOR</th><th>ID</th><th>SECTOR</th><th>STAT 1</th><th>STAT 2</th><th>STAT 3</th><th>STAT 4</th><th>STAT 5</th><th>STAT 6</th></tr></thead>
    <tbody>
      <tr><td>FACTOR 1</td><td>MODEL 1</td><td>MATERIALS</td><td>-1.4</td><td>0.1</td><td>-3.1</td><td>0.7</td><td>30.2</td><td>0.9</td></tr>
      <tr><td>FACTOR 2</td><td>MODEL 1</td><td>MATERIALS</td><td>2.8</td><td>0.1</td><td>6.1</td><td>100</td><td>30.2</td><td>0.9</td></tr>
      <tr><td>FACTOR 3</td><td>MODEL 1</td><td>MATERIALS</td><td>-3.7</td><td>2.7</td><td>-7.2</td><td>100</td><td>30.2</td><td>0.9</td></tr>
      <tr><td>FACTOR 4</td><td>MODEL 2</td><td>MATERIALS</td><td>2.8</td><td>0.2</td><td>2.7</td><td>0.5</td><td>30.9</td><td>0.5</td></tr>
      <tr><td>FACTOR 5</td><td>MODEL 2</td><td>MATERIALS</td><td>0.8</td><td>0.3</td><td>2.5</td><td>0.5</td><td>30.9</td><td>0.5</td></tr>
    </tbody>
  </table>
  <p class="footnote" style="top:463px">© Copy rights Pellworth Engines. All rights reserved 2019</p>
  <p class="code" style="left:1029px;top:468px">C41</p>
</section>

<section class="screen screen--selection">
  <header class="topbar">
    <div class="brand">PELLWORTH ENGINES</div>
    <div class="pill" style="left:550px;top:29px;width:199px">Number of selected factors: 3</div>
    <nav class="views" style="left:788px"><span class="active">FACTORS</span><span>250D</span><span>83D</span><span>42D</span></nav>
  </header>
  <nav class="tabs" style="top:87px">
    <div class="tab"><svg viewBox="0 0 20 20"><path d="M10 2 1 10h3v8h4.5v-5h3v5H16v-8h3z"/></svg>MODELS</div>
    <div class="tab"><svg viewBox="0 0 20 20"><circle cx="10" cy="10" r="7.5" fill="none" stroke="#fff" stroke-width="4" stroke-dasharray="3 2.9"/><circle cx="10" cy="10" r="6"/><circle cx="10" cy="10" r="2.3" fill="#f5b03b"/></svg>SENSITIVITIES</div>
    <div class="tab"><svg viewBox="0 0 20 20"><path d="M10 18 2.3 10.3A4.6 4.6 0 0 1 10 4a4.6 4.6 0 0 1 7.7 6.3z"/></svg>FAVORITES</div>
  </nav>
  <table class="grid grid--selection">
    <thead><tr><th>ID</th><th>STAT 1</th><th>STAT 2</th><th>STAT 3</th><th>STAT 4</th></tr></thead>
    <tbody>
      <tr><td>FACTOR 1</td><td>2.8</td><td>0.094</td><td>6.1</td><td>100</td></tr>
      <tr><td>FACTOR 2</td><td>-1.4</td><td>0.085</td><td>-3.1</td><td>0.7</td></tr>
      <tr><td>FACTOR 3</td><td>-3.7</td><td>2.7</td><td>-7.2</td><td>100</td></tr>
    </tbody>
  </table>
  <p class="footnote" style="top:376px">© Copy rights Pellworth Engines. All rights reserved 2019</p>
  <p class="code" style="left:1034px;top:377px">C41</p>
</section>

</body>
</html>
```